Beauty Therapy Web Design

I need a web page design for a small beauty therapy clinic, the owner is currently the only beauty therapist working there.
We require the following pages:
Home
About
Treatments
Nails
Courses
Contact
I will attach the clinics business card, treatment menu and signage so that you get a feeling for the branding colours etc.
This is the first website for the beauty therapist, she would like to attract new clients and also tourists that come in on the cruise ships. The thing that sets her apart from other clinics is that she welcomes texting for appointments.
I have selected refundable because I have never done this before so I don't know what to expect, I have the full intention of going through with it as long as I get a good design.
Feel free to ask for further information
Reason: Project extended as I am away for work and am unable to meet with the owner.
Target Market(s)
Females 18 to 50
Industry/Entity Type
Business
Look and feel

```html
<!DOCTYPE html>
<html lang="en">
<head>
<meta charset="utf-8">
<title>Lumera Beauty Therapy</title>
<link rel="stylesheet" href="https://fonts.googleapis.com/css2?family=Boogaloo&family=Comic+Neue:wght@700&family=Open+Sans:wght@400;600&family=Tinos&family=Lobster&display=swap">
<style>
  :root {
    --pink-page: #fbd0f2;
    --pink-deep: #f6b8ea;
    --orchid: #c45bcf;
    --orchid-dark: #a23fb5;
    --frame-purple: #c66bd0;
    --magenta-line: #e046e0;
    --ink: #1a1a1a;
    --grey-line: #444;
    --panel: #ffffff;
    --button-dark: #2d2d2d;
    --button-light: #6a6a6a;
    --sky-blue: #1a8ff0;
  }
  * { margin: 0; padding: 0; box-sizing: border-box; }
  html, body { width: 900px; height: 1200px; overflow: hidden; background: #ffffff; }
  body { position: relative; font-family: "Open Sans", Arial, sans-serif; color: var(--ink); }

  .page {
    position: absolute; left: 13px; top: 13px; width: 875px; height: 1174px;
    border: 2px solid #b34fb9;
    background:
      radial-gradient(ellipse 420px 260px at 450px 60px, rgba(255,255,255,0.95), rgba(255,255,255,0) 70%),
      linear-gradient(90deg, #fde6f8 0%, var(--pink-page) 35%, var(--pink-page) 70%, var(--pink-deep) 100%);
    box-shadow: 3px 3px 6px rgba(0,0,0,0.35);
  }

  .brand {
    position: absolute; left: 26px; top: 50px;
    display: flex; align-items: center; gap: 10px;
    font-family: "Boogaloo", cursive; font-size: 44px; line-height: 1; color: var(--orchid);
  }
  .brand-dot { width: 22px; height: 22px; border-radius: 50%; background: var(--orchid); }

  .main-nav, .footer-nav { position: absolute; display: flex; align-items: center; }
  .main-nav { right: 11px; top: 75px; font-size: 18px; }
  .main-nav a, .footer-nav a { color: var(--ink); text-decoration: none; }
  .main-nav .sep { margin: 0 10px; }
  .footer-nav { right: 6px; top: 1140px; font-size: 15px; }
  .footer-nav .sep { margin: 0 8px; }
  .copyright { position: absolute; left: 10px; top: 1142px; font-size: 13px; }

  .hero {
    position: absolute; left: 60px; top: 120px; width: 754px; height: 250px;
    background: var(--frame-purple); border-radius: 4px;
    box-shadow: 2px 3px 5px rgba(0,0,0,0.35);
  }
  .hero-photo {
    position: absolute; left: 11px; top: 11px; width: 732px; height: 227px;
    background: linear-gradient(90deg, #6b4a3c 0%, #c79a85 18%, #e9d3c9 34%, #f6ece7 55%, #fbf3ee 100%);
  }
  .hero-dots { position: absolute; right: 24px; top: 12px; display: flex; gap: 5px; }
  .hero-dots span { width: 13px; height: 13px; border-radius: 50%; background: #cfcfcf; border: 1px solid #999; }
  .hero-dots span.active { background: #666; }
  .hero-title { position: absolute; left: 397px; top: 37px; font-family: "Comic Neue", sans-serif; font-weight: 700; font-size: 38px; color: var(--sky-blue); }
  .hero-sub { position: absolute; left: 417px; top: 82px; font-family: "Comic Neue", sans-serif; font-weight: 700; font-size: 23px; line-height: 22px; color: #111; }
  .hero-name { position: absolute; right: 24px; bottom: 14px; font-family: "Boogaloo", cursive; font-size: 36px; color: var(--orchid); }

  .content {
    position: absolute; left: 62px; top: 376px; width: 752px; height: 724px;
    background: var(--panel); border-radius: 9px; border: 1px solid #bbb;
    box-shadow: 2px 3px 5px rgba(0,0,0,0.4);
  }

  .section-title { position: absolute; font-family: "Boogaloo", cursive; color: var(--orchid); white-space: nowrap; }
  .welcome-title { left: 25px; top: 28px; font-size: 27px; }
  .welcome-text {
    position: absolute; left: 25px; top: 63px; width: 400px;
    font-family: "Comic Neue", sans-serif; font-weight: 700; font-size: 13.5px; line-height: 22px;
  }
  .read-more { position: absolute; left: 353px; top: 172px; font-family: "Comic Neue", sans-serif; font-weight: 700; font-size: 15px; color: var(--orchid); }
  .divider-v { position: absolute; width: 1px; background: var(--grey-line); }
  .divider-h { position: absolute; height: 1px; background: var(--grey-line); left: 55px; width: 663px; }

  .photo-box { position: absolute; }
  .calendar { left: 561px; top: 24px; width: 186px; height: 129px; background: linear-gradient(135deg, #9a9a9a, #cfcac2 45%, #7f7f7f); }
  .pin { position: absolute; left: 658px; top: 14px; width: 16px; height: 16px; border-radius: 50%; background: #e0308f; }

  .btn {
    position: absolute; display: flex; align-items: center; justify-content: center;
    background: linear-gradient(180deg, var(--button-light), var(--button-dark) 55%, #111);
    color: #fff; border-radius: 5px; border: 1px solid #999;
    box-shadow: 1px 2px 3px rgba(0,0,0,0.4);
  }
  .btn-appointment { left: 542px; top: 160px; width: 213px; height: 34px; font-family: "Comic Neue", sans-serif; font-weight: 700; font-size: 15px; }
  .btn-more { top: 489px; width: 96px; height: 28px; font-size: 13px; }

  .col-title { top: 237px; font-size: 24px; transform: translateX(-50%); }
  .spa-photo { left: 38px; top: 264px; width: 243px; height: 216px; background: linear-gradient(160deg, #e7c9b6, #b98c74 45%, #f4e9e6 75%, #f2c4d6); }
  .product-photo { left: 518px; top: 268px; width: 240px; height: 213px; background: linear-gradient(180deg, #ffffff, #eef2f5 50%, #e4a6c4 85%); box-shadow: 1px 2px 5px rgba(0,0,0,0.45); }

  .services-list { position: absolute; left: 318px; top: 282px; list-style: none; font-family: "Tinos", serif; font-size: 26px; line-height: 28px; }

  .gallery-title { left: 50%; top: 550px; transform: translateX(-50%); font-size: 24px; }
  .gallery {
    position: absolute; left: 38px; top: 584px; width: 704px; height: 147px;
    border: 1px solid #888; border-radius: 8px; background: #fff;
    box-shadow: 1px 3px 4px rgba(0,0,0,0.35);
  }
  .gallery-item { position: absolute; top: 19px; width: 216px; height: 109px; border: 2px solid var(--magenta-line); }
  .gallery-item.one { left: 19px; background: linear-gradient(90deg, #f7f4f2, #d8b29c 45%, #a6475a 70%, #f5f1ef); }
  .gallery-item.two { left: 246px; background: linear-gradient(180deg, #8b6f57, #d4ad92 55%, #f4efe8); }
  .gallery-item.three { left: 470px; background: linear-gradient(135deg, #f6f2f3, #e3c6bf 50%, #f9f6f7); }
  .gallery-arrow { position: absolute; top: 1030px; }
</style>
</head>
<body>
<div class="page">
  <div class="brand"><span class="brand-dot"></span>Lumera</div>

  <nav class="main-nav">
    <a href="#">Home</a><span class="sep">|</span>
    <a href="#">About</a><span class="sep">|</span>
    <a href="#">Services</a><span class="sep">|</span>
    <a href="#">Treatment</a><span class="sep">|</span>
    <a href="#">Courses</a><span class="sep">|</span>
    <a href="#">Contact Us</a>
  </nav>

  <section class="hero">
    <div class="hero-photo" role="img" aria-label="Portrait of a smiling woman resting her chin on her hand against a soft bokeh background"></div>
    <div class="hero-dots"><span class="active"></span><span></span><span></span><span></span></div>
    <div class="hero-title">Beautify</div>
    <div class="hero-sub">With Your<br>Beauty Therapist</div>
    <div class="hero-name">Lumera</div>
  </section>

  <main class="content">
    <h2 class="section-title welcome-title">Welcome to Our Site:</h2>
    <p class="welcome-text">Relax and unwind at our friendly clinic. We offer facials, waxing, nails and lash treatments in a calm, private space. Text us anytime to book your visit today.</p>
    <a class="read-more">Read More &gt;&gt;&gt;</a>
    <div class="divider-v" style="left:474px; top:18px; height:164px;"></div>

    <div class="photo-box calendar" role="img" aria-label="Desk calendar blocks showing appointment dates"></div>
    <span class="pin"></span>
    <a class="btn btn-appointment">Take Your Appoinment Now</a>

    <div class="divider-h" style="top:210px;"></div>

    <h2 class="section-title col-title" style="left:138px;">Popular Services</h2>
    <h2 class="section-title col-title" style="left:391px;">Our Services</h2>
    <h2 class="section-title col-title" style="left:637px;">Our Product</h2>

    <div class="photo-box spa-photo" role="img" aria-label="Woman relaxing on a spa towel with flower petals"></div>
    <div class="divider-v" style="left:298px; top:297px; height:167px;"></div>
    <ul class="services-list">
      <li>~ Facial</li>
      <li>~ Waxing</li>
      <li>~ Gail Nails</li>
      <li>~ Manicures</li>
      <li>~ Eye Lash</li>
      <li>~ Eye Brow</li>
      <li>~ Spray Tants</li>
    </ul>
    <div class="divider-v" style="left:507px; top:297px; height:167px;"></div>
    <div class="photo-box product-photo" role="img" aria-label="Skincare bottles and tubes beside a pink cosmetic bag"></div>

    <a class="btn btn-more" style="left:181px;">More &gt;&gt;&gt;</a>
    <a class="btn btn-more" style="left:394px;">More &gt;&gt;&gt;</a>
    <a class="btn btn-more" style="left:658px;">More &gt;&gt;&gt;</a>

    <div class="divider-h" style="top:543px;"></div>
    <h2 class="section-title gallery-title">PHOTO GALLERY</h2>

    <div class="gallery">
      <div class="gallery-item one" role="img" aria-label="Woman wrapped in a towel after a body treatment"></div>
      <div class="gallery-item two" role="img" aria-label="Therapist giving a herbal compress massage"></div>
      <div class="gallery-item three" role="img" aria-label="Manicured hands with rings"></div>
    </div>
  </main>

  <svg class="gallery-arrow" style="left:74px;" width="28" height="28" viewBox="0 0 28 28" aria-hidden="true">
    <circle cx="14" cy="14" r="13" fill="#e37be6" stroke="#fff" stroke-width="2"/>
    <path d="M17 7 L9 14 L17 21 Z" fill="#fff"/>
  </svg>
  <svg class="gallery-arrow" style="left:777px;" width="28" height="28" viewBox="0 0 28 28" aria-hidden="true">
    <circle cx="14" cy="14" r="13" fill="#e37be6" stroke="#fff" stroke-width="2"/>
    <path d="M11 7 L19 14 L11 21 Z" fill="#fff"/>
  </svg>

  <footer>
    <p class="copyright">Copyright © Brightline Studio 2012</p>
    <nav class="footer-nav">
      <a href="#">Home</a><span class="sep">|</span>
      <a href="#">About</a><span class="sep">|</span>
      <a href="#">Services</a><span class="sep">|</span>
      <a href="#">Treatment</a><span class="sep">|</span>
      <a href="#">Courses</a><span class="sep">|</span>
      <a href="#">Contact Us</a>
    </nav>
  </footer>
</div>
</body>
</html>
```